RWT Fittings Ltd Business Cards

We need a business card with our business logo. We provide window and door installations on high-rises in west coast British Colombia, Canada.

I would like my business information and details on one side of the card, and the other side the company name with logo

Target Market(s)

General Contractors

Industry/Entity Type

Construction

Contact Information for Business Card

one side i want my company name and logo in the dark theme logo that i provided

Requirements
Must have
• Marco Peltieri, 16045518293, RWTFittings@mailbox-demo.com, 1407-5194 Linden Row Burnaby BC, V5H 2K9, Owner & Manager

```html
<!DOCTYPE html>
<html lang="en">
<head>
<meta charset="utf-8">
<title>RWT Fittings Ltd — Business Card</title>
<link rel="stylesheet" href="https://fonts.googleapis.com/css2?family=Open+Sans:wght@400;600;700&display=swap">
<style>
  :root {
    --page-bg: #e9e6e2;
    --card-dark: #1f1f20;
    --card-dark-edge: #2a2a2b;
    --card-glass: #5d5c5b;
    --accent-teal: #1f8fa6;
    --accent-teal-deep: #177a90;
    --text-light: #d9d2c8;
    --brand-grey: #a8a39b;
  }
  * { box-sizing: border-box; margin: 0; padding: 0; }
  html, body {
    width: 1200px; height: 1047px; overflow: hidden;
    background: var(--page-bg);
    font-family: "Open Sans", Arial, sans-serif;
  }
  .business-card {
    position: absolute;
    left: 120px; top: 261px;
    width: 960px; height: 524px;
    border-radius: 26px;
    overflow: hidden;
    background: linear-gradient(160deg, var(--card-dark-edge), var(--card-dark) 60%);
    box-shadow: 0 18px 40px rgba(0,0,0,0.18);
  }
  .card-shapes { position: absolute; inset: 0; }
  .brand-block {
    position: absolute;
    left: 106px; top: 226px;
    display: flex; align-items: center; gap: 14px;
  }
  .brand-mark {
    width: 44px; height: 44px;
    background: var(--brand-grey);
  }
  .brand-name {
    font-weight: 600; font-size: 34px;
    color: var(--accent-teal);
    letter-spacing: 0.5px;
    white-space: nowrap;
  }
  .divider {
    position: absolute;
    left: 456px; top: 133px;
    width: 3px; height: 254px;
    background: var(--accent-teal);
  }
  .contact-block {
    position: absolute;
    left: 491px; top: 126px;
    color: var(--text-light);
  }
  .person-name {
    font-weight: 700; font-size: 35px;
    color: var(--accent-teal);
    line-height: 1.2;
    letter-spacing: 0.5px;
  }
  .person-role {
    font-size: 24px; line-height: 1.2;
    margin-left: 2px;
  }
  .contact-line {
    display: flex; align-items: center; gap: 10px;
    font-size: 24px; line-height: 34px;
  }
  .contact-list { margin-top: 26px; }
  .contact-icon { width: 22px; height: 22px; flex: none; }
  .address { margin-top: 30px; font-size: 24px; line-height: 34px; }
</style>
</head>
<body>
  <div class="business-card">
    <svg class="card-shapes" viewBox="0 0 960 524" width="960" height="524" aria-hidden="true">
      <path d="M0,0 L395,0 Q140,110 0,262 Z" fill="var(--card-glass)" opacity="0.75"/>
      <path d="M700,524 Q885,430 960,262 L960,524 Z" fill="var(--accent-teal-deep)"/>
    </svg>

    <div class="brand-block">
      <span class="brand-mark"></span>
      <span class="brand-name">RWT Fittings Ltd</span>
    </div>

    <div class="divider"></div>

    <div class="contact-block">
      <h1 class="person-name">Marco Peltieri</h1>
      <p class="person-role">Owner &amp; Manager</p>

      <div class="contact-list">
        <p class="contact-line">
          <svg class="contact-icon" viewBox="0 0 24 24" aria-hidden="true">
            <path d="M6.6 10.8a15.1 15.1 0 0 0 6.6 6.6l2.2-2.2c.3-.3.7-.4 1-.2 1.1.4 2.3.6 3.6.6.6 0 1 .4 1 1V20c0 .6-.4 1-1 1A17 17 0 0 1 3 4c0-.6.4-1 1-1h3.5c.6 0 1 .4 1 1 0 1.3.2 2.5.6 3.6.1.3 0 .7-.2 1z" fill="var(--accent-teal)"/>
          </svg>
          16045518293
        </p>
        <p class="contact-line">
          <svg class="contact-icon" viewBox="0 0 24 24" aria-hidden="true">
            <rect x="2" y="5" width="20" height="14" rx="2" fill="var(--accent-teal)"/>
            <path d="M3 6.5l9 6.5 9-6.5" fill="none" stroke="var(--card-dark)" stroke-width="1.8"/>
          </svg>
          RWTFittings@mailbox-demo.com
        </p>
      </div>

      <p class="address">1407-5194 Linden Row<br>Burnaby BC, V5H 2K9</p>
    </div>
  </div>
</body>
</html>
```